RWT Fittings Ltd Business Cards

We need a business card with our business logo. We provide window and door installations on high-rises in west coast British Colombia, Canada.

I would like my business information and details on one side of the card, and the other side the company name with logo

Target Market(s)

General Contractors

Industry/Entity Type

Construction

Contact Information for Business Card

one side i want my company name and logo in the dark theme logo that i provided

Requirements
Must have
• Marco Peltieri, 16045518293, RWTFittings@mailbox-demo.com, 1407-5194 Linden Row Burnaby BC, V5H 2K9, Owner & Manager

```html
<!DOCTYPE html>
<html lang="en">
<head>
<meta charset="utf-8">
<title>RWT Fittings Ltd – Business Cards</title>
<link rel="stylesheet" href="https://fonts.googleapis.com/css2?family=Roboto:wght@400;500;700;900&display=swap">
<style>
  :root {
    --backdrop: #232323;
    --brand-blue: #27a8e1;
    --card-dark: #202024;
    --ink-dark: #1d1d21;
    --surname-grey: #9b9b9d;
    --text-light: #ffffff;
  }
  * { box-sizing: border-box; margin: 0; padding: 0; }
  html, body {
    width: 1200px;
    height: 780px;
    overflow: hidden;
    background: var(--backdrop);
    font-family: "Roboto", Arial, sans-serif;
  }
  .card-set {
    position: absolute;
    inset: 0;
    display: flex;
    align-items: center;
    justify-content: center;
    gap: 40px;
  }
  .card {
    position: relative;
    width: 540px;
    height: 310px;
    box-shadow: 0 14px 30px rgba(0, 0, 0, 0.55);
    overflow: hidden;
  }

  /* Front: company name */
  .card--front {
    background: var(--brand-blue);
    display: flex;
    align-items: center;
    justify-content: center;
    gap: 14px;
  }
  .brand-mark {
    width: 34px;
    height: 34px;
    background: var(--ink-dark);
  }
  .brand-name {
    font-weight: 900;
    font-size: 38px;
    letter-spacing: 1px;
    color: var(--ink-dark);
    text-transform: uppercase;
  }

  /* Back: contact details */
  .card--back {
    background: var(--card-dark);
    color: var(--text-light);
  }
  .card--back::after {
    content: "";
    position: absolute;
    left: 0; right: 0; bottom: 0;
    height: 6px;
    background: var(--brand-blue);
  }
  .person {
    position: absolute;
    left: 48px;
    top: 128px;
  }
  .person-name {
    font-weight: 900;
    font-size: 30px;
    line-height: 1;
    white-space: nowrap;
  }
  .person-name .given { color: var(--brand-blue); }
  .person-name .family { color: var(--surname-grey); }
  .person-role {
    margin-top: 4px;
    padding-left: 112px;
    font-weight: 700;
    font-size: 13px;
    color: var(--text-light);
  }
  .divider {
    position: absolute;
    left: 300px;
    top: 92px;
    width: 1.5px;
    height: 108px;
    background: var(--text-light);
  }
  .contact-list {
    position: absolute;
    left: 322px;
    top: 112px;
    list-style: none;
    font-size: 13px;
    line-height: 1;
  }
  .contact-item {
    display: flex;
    align-items: center;
    gap: 8px;
    margin-bottom: 10px;
  }
  .contact-icon { width: 14px; height: 14px; flex: none; }
  .address {
    position: absolute;
    left: 0; right: 0;
    top: 250px;
    text-align: center;
    font-size: 14px;
    padding-left: 80px;
  }
</style>
</head>
<body>
  <main class="card-set">
    <section class="card card--front" aria-label="Business card front">
      <span class="brand-mark" aria-hidden="true"></span>
      <span class="brand-name">RWT Fittings Ltd</span>
    </section>

    <section class="card card--back" aria-label="Business card back">
      <div class="person">
        <p class="person-name"><span class="given">Marco</span> <span class="family">Peltieri</span></p>
        <p class="person-role">Owner &amp; Manager</p>
      </div>
      <span class="divider" aria-hidden="true"></span>
      <ul class="contact-list">
        <li class="contact-item">
          <svg class="contact-icon" viewBox="0 0 24 24" aria-hidden="true"><path fill="#27a8e1" d="M6.6 10.8a15.1 15.1 0 0 0 6.6 6.6l2.2-2.2c.3-.3.7-.4 1-.2 1.1.4 2.3.6 3.6.6.6 0 1 .4 1 1V20c0 .6-.4 1-1 1A17 17 0 0 1 3 4c0-.6.4-1 1-1h3.5c.6 0 1 .4 1 1 0 1.3.2 2.5.6 3.6.1.3 0 .7-.2 1z"/></svg>
          <span>1604 551 8293</span>
        </li>
        <li class="contact-item">
          <svg class="contact-icon" viewBox="0 0 24 24" aria-hidden="true"><path fill="#27a8e1" d="M2 5h20v14H2z"/><path fill="none" stroke="#202024" stroke-width="2" d="M2 5l10 8 10-8"/></svg>
          <span>RWTFittings@mailbox-demo.com</span>
        </li>
      </ul>
      <p class="address">1407-5194 Linden Row Burnaby BC, V5H 2K9</p>
    </section>
  </main>
</body>
</html>
```